National Mission Critical Construction Contractor needs Stationery Design to make a bold statement

We are a small commercial construction company, working primarily in mission critical facilities across the U.S.. We have exciting corporate changes going an and a new logo and office space so we need new stationery. The final design should incorporate our new logo and invoke a fresh, high-tech feel while looking simple and modern.

Industry/Entity Type

Construction

Contact Information for Business Card

We are required to list our state licensing qualifications on the back of our card.

Font styles to use
Sans Serif

Requirements
Must have
• We need to have a design for second page of stationery, envelopes both standard and with a window and for a 3 x 4 notepad.

```html
<!DOCTYPE html>
<html lang="en">
<head>
<meta charset="utf-8">
<title>Slate Creek Stationery</title>
<link rel="stylesheet" href="https://fonts.googleapis.com/css2?family=Montserrat:wght@400;600&display=swap">
<style>
:root{
  --blue:#0b72b9;
  --green:#8dc63f;
  --paper:#ffffff;
  --backdrop:#c4c5c7;
  --shadow:0 6px 14px rgba(0,0,0,.35);
}
*{margin:0;padding:0;box-sizing:border-box}
html,body{width:1200px;height:927px;overflow:hidden}
body{background:var(--backdrop);font-family:"Montserrat",sans-serif;position:relative}
.sheet{position:absolute;box-shadow:var(--shadow);overflow:hidden}

/* letterhead */
.letterhead{left:149px;top:48px;width:441px;height:568px;background:var(--paper)}
.letterhead .green-tab{position:absolute;left:0;top:16px;width:55px;height:58px;background:var(--green)}
.brand{display:flex;align-items:center;gap:8px;color:var(--blue);font-weight:600;letter-spacing:.5px;white-space:nowrap}
.brand .dot{flex:none;border-radius:50%;background:var(--blue)}
.letterhead .brand{position:absolute;left:36px;top:28px;font-size:22px}
.letterhead .brand .dot{width:44px;height:44px;border:4px solid var(--paper)}
.contact{position:absolute;left:293px;top:16px;padding-left:13px;border-left:1px solid var(--blue);
  color:var(--blue);font-size:10px;line-height:12px}
.contact .gap{height:3px}
.contact li{list-style:none;display:flex;align-items:center;gap:5px}
.contact svg{width:7px;height:7px;flex:none}
.contact b{font-weight:600}
.band-bottom{position:absolute;left:0;right:0;bottom:0}
.letterhead .band-bottom{height:14px;background:var(--blue)}

/* folder */
.folder{left:610px;top:48px;width:441px;height:568px;background:var(--blue)}
.folder .brand-large{position:absolute;left:0;right:0;top:262px;text-align:center;color:var(--paper);
  font-weight:600;font-size:38px;letter-spacing:1px}
.web{position:absolute;left:0;right:0;text-align:center;color:var(--paper);font-size:11.5px;letter-spacing:.4px}
.web b{font-weight:600}
.folder .web{top:526px}
.folder .band-bottom{height:14px;background:var(--green)}

/* envelope front */
.envelope-front{left:135px;top:644px;width:454px;height:234px;background:var(--paper)}
.envelope-front .flap{position:absolute;left:0;top:0;width:100%;height:30px;background:var(--blue);border-radius:14px 14px 0 0}
.envelope-front .brand{position:absolute;left:0;right:0;top:106px;justify-content:center;font-size:22px}
.envelope-front .brand .dot{width:40px;height:40px}
.envelope-front .address{position:absolute;left:0;right:0;top:202px;text-align:center;color:var(--blue);font-size:9.5px}
.envelope-front .band-bottom{height:12px;background:var(--blue)}

/* envelope back */
.envelope-back{left:610px;top:672px;width:454px;height:206px;background:var(--blue)}
.envelope-back .flap{position:absolute;left:0;top:0;width:100%;height:30px;background:var(--green);border-radius:0 0 14px 14px}
.envelope-back .brand-small{position:absolute;left:0;right:0;top:98px;text-align:center;color:var(--paper);font-weight:600;font-size:22px;letter-spacing:1px}
.envelope-back .web{top:176px;font-size:11px}
.envelope-back .band-bottom{height:12px;background:var(--green)}
</style>
</head>
<body>

<section class="sheet letterhead" aria-label="Letterhead">
  <div class="green-tab"></div>
  <div class="brand"><span class="dot"></span>SLATE CREEK</div>
  <ul class="contact">
    <li>418B W. Cedar Hollow Rd.</li>
    <li>Millbrook, TX. 77510</li>
    <li class="gap"></li>
    <li><svg viewBox="0 0 10 10"><path d="M2 1h2l1 2-1.2 1a5 5 0 0 0 2.2 2.2L7 5l2 1v2c0 .6-.5 1-1 1A8 8 0 0 1 1 2c0-.5.4-1 1-1z" fill="#8dc63f"/></svg>+1.555.204.3187</li>
    <li><svg viewBox="0 0 10 10"><rect x="1" y="2" width="8" height="6" fill="none" stroke="#8dc63f" stroke-width="1.2"/><path d="M1 2l4 3 4-3" fill="none" stroke="#8dc63f" stroke-width="1.2"/></svg>info@slatecreek.com</li>
    <li><svg viewBox="0 0 10 10"><circle cx="5" cy="5" r="4" fill="none" stroke="#8dc63f" stroke-width="1.2"/><path d="M1 5h8M5 1c-2 2.5-2 5.5 0 8M5 1c2 2.5 2 5.5 0 8" fill="none" stroke="#8dc63f" stroke-width=".9"/></svg>www.<b>slatecreek</b>.com</li>
  </ul>
  <div class="band-bottom"></div>
</section>

<section class="sheet folder" aria-label="Presentation folder">
  <div class="brand-large">SLATE CREEK</div>
  <p class="web">www.<b>slatecreek</b>.com</p>
  <div class="band-bottom"></div>
</section>

<section class="sheet envelope-front" aria-label="Envelope front">
  <div class="flap"></div>
  <div class="brand"><span class="dot"></span>SLATE CREEK</div>
  <p class="address">418B W. Cedar Hollow Rd. Millbrook, TX. 77510</p>
  <div class="band-bottom"></div>
</section>

<section class="sheet envelope-back" aria-label="Envelope back">
  <div class="flap"></div>
  <div class="brand-small">SLATE CREEK</div>
  <p class="web">www.<b>slatecreek</b>.com</p>
  <div class="band-bottom"></div>
</section>

</body>
</html>
```